Creative, fresh business card design for Ripplecraft Facades

We need a fresh, creative business card design for Ripplecraft Facades. We are the manufacturer of Ripplecraft Facades in Australia. Wall panels are 2400 x 1200mm panels made from MDF and feature 3D patterns on the face of the panel. The colours to be used are green, silver/grey and white RGB
Red 187
Green 207
Blue 65.

An idea is to possibly use a watermark of one of our designs as a background (like on the "Grids" design on the left hand side of page 2 of our brochure).

Target Market(s)

Interior designers, architects, builders and home renovators

Industry/Entity Type

Business

Contact Information for Business Card

Details to go on the card are:
Our logo (attached),
Slogan: "Decorative panels for interiors and exteriors",
Contact name,
Position,
Mobile phone number,
Business address,
Business phone,
Business fax,
Website and
Email address.

I have attached a few images of our panels and our brochure for reference.

The colours of the business card should feature our logo colours which are: RGB
Red 187
Green 207
Blue 65

Requirements
Must have
• Very modern fonts and design. Some of the designs shown especially the "Prisms" design which is a popular design.
Nice to have
• Creative but simple design. Very contemporary.
Should not have
• Anything ornate or old fashioned.

```html
<!DOCTYPE html>
<html lang="en">
<head>
<meta charset="utf-8">
<title>Ripplecraft Facades – Business Card</title>
<link rel="stylesheet" href="https://fonts.googleapis.com/css2?family=PT+Sans:wght@400;700&family=Arimo:wght@400&display=swap">
<style>
  :root {
    --stage: #000000;
    --card: #2f3032;
    --card-edge: #38393b;
    --brand-green: #bbcf41;
    --silver: #9a9b9d;
    --text-light: #f2f2f2;
    --divider: #3c3d40;
  }
  * { margin: 0; padding: 0; box-sizing: border-box; }
  html, body {
    width: 1200px; height: 900px; overflow: hidden;
    background: var(--stage);
  }
  .stage { position: relative; width: 1200px; height: 900px; }
  .card {
    position: absolute; top: 271px; width: 456px; height: 282px;
    border-radius: 14px; background: var(--card); overflow: hidden;
  }
  .card--front { left: 137px; }
  .card--back { left: 627px; }

  /* front */
  .brand-lockup {
    position: absolute; left: 50px; top: 396px; top: 125px;
    display: flex; align-items: center; gap: 8px;
  }
  .brand-mark { width: 22px; height: 22px; background: var(--brand-green); }
  .brand-name {
    font-family: "PT Sans", sans-serif; font-weight: 700;
    font-size: 17px; color: var(--brand-green); white-space: nowrap;
  }
  .divider {
    position: absolute; left: 225px; top: 80px; width: 1px; height: 150px;
    background: var(--divider);
  }
  .details {
    position: absolute; left: 255px; top: 41px;
    font-family: "PT Sans", sans-serif; color: var(--text-light);
    font-size: 13px; line-height: 16px;
  }
  .contact-name { color: var(--brand-green); font-weight: 700; font-size: 17px; line-height: 20px; }
  .contact-role { margin-bottom: 19px; }
  .address { margin-bottom: 14px; }
  .contact-list { list-style: none; }
  .contact-list li { display: flex; align-items: center; gap: 7px; height: 19px; }
  .contact-list svg { width: 10px; height: 10px; fill: var(--brand-green); flex: none; }

  /* back */
  .pattern-field {
    position: absolute; inset: 0;
    background:
      radial-gradient(ellipse at 50% 20%, rgba(255,255,255,0.05), transparent 60%),
      linear-gradient(160deg, #343537 0%, #2b2c2e 50%, #323335 100%);
  }
  .back-lockup {
    position: absolute; left: 0; right: 0; top: 135px;
    display: flex; justify-content: center; align-items: center; gap: 12px;
  }
  .back-lockup .brand-mark { width: 34px; height: 34px; }
  .back-lockup .brand-name { font-size: 30px; }
  .tagline {
    position: absolute; left: 0; right: 0; top: 191px; text-align: center;
    font-family: "Arimo", sans-serif; font-size: 13px; line-height: 16px;
    letter-spacing: 2.6px; color: var(--silver);
  }
</style>
</head>
<body>
<main class="stage">
  <section class="card card--front">
    <div class="brand-lockup">
      <span class="brand-mark"></span>
      <span class="brand-name">Ripplecraft Facades</span>
    </div>
    <div class="divider"></div>
    <div class="details">
      <p class="contact-name">Marcus Elden</p>
      <p class="contact-role">Managing Director</p>
      <p class="address">12345, Address Goes Here<br>Country Name, 123456</p>
      <ul class="contact-list">
        <li><svg viewBox="0 0 10 10"><path d="M2.5 0h5v10h-5z M3.5 1v7h3V1z" fill-rule="evenodd"/></svg>123-456-7890</li>
        <li><svg viewBox="0 0 10 10"><path d="M2 0.5l2 2-1 1.2c.8 1.5 1.8 2.5 3.3 3.3l1.2-1 2 2-1.3 1.5C4.5 9 1 5.5.5 1.8z"/></svg>(044)-456-7890</li>
        <li><svg viewBox="0 0 10 10"><path d="M2.5 0h4v3h-4z M1 3.5h8v6H1z"/></svg>123-456-7890</li>
        <li><svg viewBox="0 0 10 10"><path d="M0.5 2h9v6h-9z" /><path d="M0.5 2l4.5 3.5L9.5 2" fill="none" stroke="#2f3032" stroke-width="1"/></svg>info@ripplecraftfacades.com</li>
        <li><svg viewBox="0 0 10 10"><circle cx="5" cy="5" r="4.5"/></svg>www.ripplecraftfacades.com</li>
      </ul>
    </div>
  </section>

  <section class="card card--back">
    <div class="pattern-field" role="img" aria-label="Faint background of a faceted 3D prism panel pattern"></div>
    <div class="back-lockup">
      <span class="brand-mark"></span>
      <span class="brand-name">Ripplecraft Facades</span>
    </div>
    <p class="tagline">decorative panels for<br>interiors &amp; landscapes</p>
  </section>
</main>
</body>
</html>
```